We would like to obtain a sales orientated brochure to promote our two models of thermal imaging cameras as a response to the current Covid 19 health issues. I have provided the text, photos and detailed product specifications , in addition to a sample competitors brochure.
BROCHURE Details : 2 sided - front side to show product, its applications in business, school, hospitals, with text details - Back page to show specifications chart and contact information for Korvel Display Group. (Melbourne -Sydney-Perth-Brisbane - 1300 618 475
Brochure should be "eye-catching" and reflect the product as a high quality, must-have technology device for todays world.

```html
<!DOCTYPE html>
<html lang="en">
<head>
<meta charset="utf-8">
<title>Thermal Scanning and Facial Recognition Camera – Korvel Display Group</title>
<link rel="stylesheet" href="https://fonts.googleapis.com/css2?family=Russo+One&family=Arvo:wght@700&family=Roboto:wght@300;400&display=swap">
<style>
  :root {
    --ink: #050507;
    --charcoal: #1c1c20;
    --pink: #c9407f;
    --pink-soft: #b8487d;
    --white: #ffffff;
    --grey-text: #d8d8dc;
    --label: #e6e6ea;
    --violet: #3a1a6e;
    --indigo: #2a2f9a;
    --magenta: #6a1a5e;
  }
  * { margin: 0; padding: 0; box-sizing: border-box; }
  html, body { width: 1200px; height: 862px; overflow: hidden; background: var(--ink); }
  .brochure {
    position: relative;
    width: 1200px;
    height: 862px;
    overflow: hidden;
    background: linear-gradient(180deg, var(--ink) 0%, var(--ink) 45%, var(--charcoal) 100%);
    font-family: "Roboto", sans-serif;
    color: var(--white);
  }
  .hero-art { position: absolute; inset: 0; }
  .title {
    position: absolute;
    left: 96px;
    top: 34px;
    font-family: "Russo One", sans-serif;
    font-size: 44px;
    line-height: 58px;
    color: var(--pink);
    letter-spacing: 0.5px;
    text-transform: uppercase;
  }
  .purpose {
    position: absolute;
    left: 80px;
    top: 258px;
    width: 228px;
    padding-left: 12px;
    border-left: 4px solid var(--pink);
  }
  .purpose-heading {
    font-family: "Arvo", serif;
    font-weight: 700;
    font-size: 17px;
    line-height: 21px;
    text-transform: uppercase;
    margin-bottom: 14px;
  }
  .purpose p {
    font-size: 10.5px;
    line-height: 18.5px;
    font-weight: 300;
    color: var(--grey-text);
    margin-bottom: 6px;
  }
  .brand {
    position: absolute;
    left: 58px;
    top: 720px;
  }
  .brand-name {
    display: flex;
    align-items: center;
    gap: 10px;
    font-size: 21px;
    font-weight: 400;
    color: #a9c8ee;
  }
  .brand-mark { width: 18px; height: 18px; background: #a9c8ee; }
  .brand-meta {
    margin-top: 10px;
    padding-left: 28px;
    font-size: 8.5px;
    line-height: 18px;
    letter-spacing: 2px;
    color: var(--grey-text);
    text-transform: uppercase;
  }
  .product-label {
    position: absolute;
    font-family: "Russo One", sans-serif;
    font-size: 16px;
    line-height: 26px;
    color: var(--label);
    text-transform: uppercase;
  }
  .label-floor { left: 950px; top: 190px; }
  .label-desk { left: 600px; top: 555px; text-align: center; }
  .contact {
    position: absolute;
    right: 70px;
    top: 745px;
    text-align: right;
  }
  .contact-call {
    font-family: "Russo One", sans-serif;
    font-size: 40px;
    color: var(--pink);
    line-height: 44px;
  }
  .contact-note {
    font-family: "Arvo", serif;
    font-weight: 700;
    font-size: 12px;
    letter-spacing: 1.5px;
    text-transform: uppercase;
    color: var(--grey-text);
    margin-top: 4px;
  }
  .contact-web {
    font-size: 20px;
    font-weight: 300;
    letter-spacing: 7px;
    color: var(--pink-soft);
    margin-top: 4px;
  }
</style>
</head>
<body>
<main class="brochure">
  <svg class="hero-art" width="1200" height="862" viewBox="0 0 1200 862" aria-hidden="false">
    <defs>
      <radialGradient id="orb-fill" cx="0.45" cy="0.55" r="0.6">
        <stop offset="0" stop-color="var(--indigo)"/>
        <stop offset="0.55" stop-color="var(--violet)"/>
        <stop offset="1" stop-color="var(--magenta)"/>
      </radialGradient>
      <linearGradient id="device-fill" x1="0" y1="0" x2="0" y2="1">
        <stop offset="0" stop-color="#d9d9de"/>
        <stop offset="0.5" stop-color="#5a6070"/>
        <stop offset="1" stop-color="#2c2c34"/>
      </linearGradient>
      <linearGradient id="stand-fill" x1="0" y1="0" x2="0" y2="1">
        <stop offset="0" stop-color="#e2e2e8"/>
        <stop offset="1" stop-color="#3a3a42"/>
      </linearGradient>
    </defs>
    <circle class="orb-ring" cx="815" cy="300" r="382" fill="none" stroke="#e8e8ec" stroke-width="3"/>
    <circle class="orb-shadow" cx="815" cy="300" r="372" fill="#0d0d12"/>
    <circle class="orb" cx="815" cy="300" r="352" fill="url(#orb-fill)"/>
    <rect role="img" aria-label="Photo of the portable reception desk thermal camera on its stand" x="640" y="30" width="170" height="510" rx="14" fill="url(#device-fill)"/>
    <rect role="img" aria-label="Photo of the portable floor standing thermal camera" x="830" y="0" width="120" height="560" rx="10" fill="url(#stand-fill)"/>
  </svg>

  <h1 class="title">Thermal Scanning<br>and Facial<br>Recognition<br>Camera</h1>

  <section class="purpose">
    <h2 class="purpose-heading">The Purpose of<br>Thermal Scanning<br>&amp; Facial Recognition</h2>
    <p>The purpose is to identify anyone walking into an establishment with a high temperature. This will reduce the likelihood of spreading any potential virus and brings some peace of mind to people in the building.</p>
    <p>We can pair your thermal camera/s with facial recognition software. Employees will check in by standing in front of the camera, which identifies them by their face in just a few seconds without contact (with or without a mask on) and simultaneously performs a thermal scan. It will record a photo of the individual, the date, the time and the temperature reading at that time of entering the building. If the camera detects a high temperature reading, it will sound an alarm in real time and send a notification to a nominated administrator/in-house security.</p>
  </section>

  <p class="product-label label-floor">Portable Floor<br>Standing Camera</p>
  <p class="product-label label-desk">Portable Camera<br>for Reception Desk</p>

  <footer class="brand">
    <div class="brand-name"><span class="brand-mark"></span>Korvel Display Group</div>
    <div class="brand-meta">Korvel Display Group<br>Melbourne-Sydney-Perth-Brisbane<br>1300 618 475</div>
  </footer>

  <section class="contact">
    <div class="contact-call">CALL 1300 618 475</div>
    <div class="contact-note">For further information and a free quote</div>
    <div class="contact-web">www.korveldisplay.com.au</div>
  </section>
</main>
</body>
</html>
```